website design for M&T Electric

A portfolio website for a high end commercial and residential electrical contracting company. The current site mandtelectric.example does not represent the current direction but the images in the gallery give you an idea of the work we do. Current logo will be uploaded shortly but is black text on white background.
Target Market(s)
General Contractors, Residential Home Owners, clients intersted in Velmora home automation.
Industry/Entity Type
Electrician
Coding
Coded - Design and coding required
Number of Pages Required
2 page
Font styles to use
Sans Serif
Colors
Designer to choose colors to be used in the design.
Requirements
Must have
- Portfolio section highlighting different service areas and products (Velmora Housepilot, etc)

```html
<!DOCTYPE html>
<html lang="en">
<head>
<meta charset="utf-8">
<title>M&amp;T Electric</title>
<link href="https://fonts.googleapis.com/css2?family=Open+Sans:wght@400;600;700;800&display=swap" rel="stylesheet">
<style>
:root{
  --orange:#f39a1e;
  --dark:#2b2b2b;
  --darker:#1f1f1f;
  --ink:#333;
  --muted:#666;
  --light:#efefef;
  --ring:#9a9a9a;
  --white:#fff;
}
*{box-sizing:border-box;margin:0;padding:0}
html,body{width:1200px;height:2948px;overflow:hidden}
body{font-family:"Open Sans",Arial,sans-serif;color:var(--ink);background:var(--white);position:relative}
section,header,footer{position:absolute;left:0;width:1200px}

/* header */
.site-header{top:0;height:48px;background:var(--white);z-index:5;box-shadow:0 2px 6px rgba(0,0,0,.25)}
.brand{position:absolute;left:0;top:0;height:48px;width:420px;background:var(--darker);clip-path:polygon(0 0,100% 0,92% 100%,0 100%);display:flex;align-items:center;padding-left:28px}
.brand span{color:var(--white);font-size:30px;font-weight:700;letter-spacing:.5px}
.main-nav{position:absolute;right:40px;top:0;height:48px;display:flex;align-items:center;gap:48px}
.main-nav a{font-size:15px;font-weight:700;color:var(--ink);text-decoration:none;text-transform:uppercase}

/* hero */
.hero{top:0;height:560px}
.hero-photo{position:absolute;inset:0;background:linear-gradient(180deg,#3e3a36 0%,#58524b 45%,#4a453f 100%)}
.hero-title{position:absolute;top:170px;width:100%;text-align:center;color:var(--white);font-size:56px;font-weight:700;letter-spacing:2px}
.hero-sub{position:absolute;top:278px;left:340px;width:520px;text-align:center;color:var(--white);font-size:17px;line-height:26px}
.hero-arrow{position:absolute;top:272px}
.hero-arrow.prev{left:26px}.hero-arrow.next{right:26px}
.hero-curve{position:absolute;left:0;bottom:0}

/* services */
.services{top:460px;height:420px}
.service{position:absolute;width:320px;text-align:center}
.service-photo{width:248px;height:248px;border-radius:50%;margin:0 auto;border:9px solid var(--ring);background:radial-gradient(circle at 50% 40%,#8a6a46,#3b2d22)}
.service.featured .service-photo{border-color:var(--orange);background:radial-gradient(circle at 50% 45%,#b47a3c,#5a3a1e)}
.service.landscape .service-photo{background:radial-gradient(circle at 50% 40%,#d9d6cf,#6d6760)}
.service h3{margin-top:24px;font-size:22px;font-weight:600;text-transform:uppercase;color:var(--ink)}
.service.featured h3{color:var(--orange)}
.service p{margin:14px auto 0;width:290px;font-size:14px;line-height:22px;color:var(--muted)}
.read-more{display:inline-flex;align-items:center;gap:8px;margin-top:16px;font-size:14px;font-weight:700;color:var(--ink);text-transform:uppercase}
.service.featured .read-more{color:var(--orange)}

/* about */
.about{top:928px;height:452px;background:var(--light);text-align:center}
.section-title{font-size:30px;font-weight:700;color:var(--orange);text-transform:uppercase;letter-spacing:1px}
.title-rule{width:70px;height:3px;background:var(--orange);margin:10px auto 0}
.about .section-title{margin-top:68px}
.about p{width:1000px;margin:26px auto 0;font-size:14px;line-height:26px;color:var(--muted)}
.about p+p{margin-top:22px}
.about-actions{margin-top:60px;display:flex;justify-content:center;gap:14px}
.btn{height:44px;padding:0 22px;font-size:14px;font-weight:700;display:flex;align-items:center;border-radius:3px}
.btn-primary{background:var(--orange);color:var(--white)}
.btn-outline{border:2px solid var(--ink);color:var(--ink);background:var(--white)}

/* gallery */
.gallery{top:1380px;height:728px;text-align:center}
.gallery .section-title{margin-top:70px}
.gallery-grid{position:absolute;left:108px;top:168px;display:grid;grid-template-columns:repeat(3,312px);grid-template-rows:220px 240px;gap:30px 22px}
.gallery-item{background:linear-gradient(160deg,#9cb2c8 0%,#b89a7e 55%,#6f6a5e 100%)}
.gallery-item:nth-child(2){background:linear-gradient(160deg,#a9b9c9,#9a6a58 60%,#5d4d44)}
.gallery-item:nth-child(3){background:linear-gradient(160deg,#9fbbd8,#c9c6bf 55%,#6e6c66)}
.gallery-item:nth-child(4){background:linear-gradient(160deg,#dce2e8,#c79679 55%,#8a7a6c)}
.gallery-item:nth-child(5){background:linear-gradient(160deg,#b9c4cf,#7a6e62 55%,#3e3a36)}
.gallery-item:nth-child(6){background:linear-gradient(160deg,#d3dde6,#a2a09a 55%,#5c5a56)}
.gallery-arrow{position:absolute;top:386px}
.gallery-arrow.prev{left:34px}.gallery-arrow.next{right:34px}

/* testimonials */
.testimonials{top:2108px;height:420px;background:var(--light);text-align:center}
.testimonials .section-title{margin-top:60px}
.testimonial{position:absolute;top:188px;width:440px;text-align:left}
.testimonial .avatar{position:absolute;left:0;top:0;width:104px;height:104px;border-radius:50%;border:4px solid var(--white);box-shadow:0 0 0 1px #ccc;background:linear-gradient(180deg,#c9b59a,#8a7056)}
.testimonial .quote{position:absolute;left:136px;top:-20px;color:var(--orange);font-size:60px;font-weight:800;line-height:1}
.testimonial h4{position:absolute;left:136px;top:30px;font-size:16px;font-weight:600;text-transform:uppercase;color:var(--ink)}
.testimonial .name{position:absolute;left:136px;top:54px;font-size:14px;color:var(--muted)}
.testimonial .stars{position:absolute;left:136px;top:78px;display:flex;gap:3px}
.testimonial p{position:absolute;left:0;top:126px;width:440px;font-size:13px;line-height:21px;color:var(--muted)}

/* footer */
.site-footer{top:2528px;height:420px;background:var(--dark);color:var(--white)}
.footer-brand{position:absolute;left:150px;top:108px;font-size:38px;font-weight:600}
.socials{position:absolute;left:150px;top:218px;display:flex;gap:10px}
.socials span{width:30px;height:30px;border:2px solid var(--white);border-radius:50%}
.footer-col{position:absolute;top:40px}
.footer-col h5{font-size:17px;font-weight:700;text-transform:uppercase;margin-bottom:20px}
.quick-links{left:388px}
.quick-links li{list-style:none;font-size:15px;line-height:29px}
.quick-links li::before{content:"› ";}
.contact{left:564px;width:210px}
.contact-row{display:flex;gap:14px;margin-bottom:22px}
.contact-row .ico{flex:none;width:34px;height:34px;border-radius:50%;background:#444;display:flex;align-items:center;justify-content:center}
.contact-row b{display:block;font-size:14px;text-transform:uppercase}
.contact-row small{display:block;font-size:12px;line-height:18px;color:#ccc}
.contact-form{left:812px;width:240px}
.form-row{display:flex;gap:10px;margin-bottom:10px}
.field{height:32px;border:1px solid #777;font-size:12px;color:#bbb;padding:7px 8px;flex:1}
.field.message{height:72px}
.btn-submit{margin-top:14px;width:120px;height:34px;background:var(--orange);color:var(--white);font-size:12px;font-weight:700;display:flex;align-items:center;justify-content:center}
.copyright{position:absolute;left:0;bottom:0;width:1200px;height:68px;border-top:1px solid #444;display:flex;align-items:center;justify-content:center;font-size:14px;color:#ddd}
</style>
</head>
<body>

<header class="site-header">
  <div class="brand"><span>M&amp;T Electric</span></div>
  <nav class="main-nav">
    <a>Home</a><a>Gallery</a><a>Specialty Services</a><a>About</a><a>Contact</a>
  </nav>
</header>

<section class="hero">
  <div class="hero-photo" role="img" aria-label="Dimmed photo of the company's shop building at dusk"></div>
  <h1 class="hero-title">M &amp; T ELECTRIC</h1>
  <p class="hero-sub">M&amp;T Electric is a full service electrical contracting shop. We offer commercial, residential, light industrial, and agricultural services.</p>
  <svg class="hero-arrow prev" width="20" height="34" viewBox="0 0 20 34"><path d="M17 2 3 17l14 15" fill="none" stroke="#fff" stroke-width="3"/></svg>
  <svg class="hero-arrow next" width="20" height="34" viewBox="0 0 20 34"><path d="M3 2l14 15L3 32" fill="none" stroke="#fff" stroke-width="3"/></svg>
  <svg class="hero-curve" width="1200" height="110" viewBox="0 0 1200 110"><path d="M0 110V70Q600-30 1200 70v40Z" fill="#fff"/></svg>
</section>

<section class="services">
  <article class="service" style="left:88px">
    <div class="service-photo" role="img" aria-label="Commercial building lit at night"></div>
    <h3>Commercial</h3>
    <p>We're Velmora Housepilot and Velmora Motorized Shades certified, as well as an authorized Voltaro generator dealer.</p>
    <span class="read-more">Read more <svg width="16" height="16" viewBox="0 0 16 16"><circle cx="8" cy="8" r="8" fill="#333"/><path d="M6 4l4 4-4 4" fill="none" stroke="#fff" stroke-width="2"/></svg></span>
  </article>
  <article class="service featured" style="left:440px">
    <div class="service-photo" role="img" aria-label="Warmly lit residential interior"></div>
    <h3>Residential</h3>
    <p>We're Velmora Housepilot and Velmora Motorized Shades certified, as well as an authorized Voltaro generator dealer.</p>
    <span class="read-more">Read more <svg width="16" height="16" viewBox="0 0 16 16"><circle cx="8" cy="8" r="8" fill="#f39a1e"/><path d="M6 4l4 4-4 4" fill="none" stroke="#fff" stroke-width="2"/></svg></span>
  </article>
  <article class="service landscape" style="left:788px">
    <div class="service-photo" role="img" aria-label="Room with motorized window shades"></div>
    <h3>Landscape</h3>
    <p>We're Velmora Housepilot and Velmora Motorized Shades certified, as well as an authorized Voltaro generator dealer.</p>
    <span class="read-more">Read more <svg width="16" height="16" viewBox="0 0 16 16"><circle cx="8" cy="8" r="8" fill="#333"/><path d="M6 4l4 4-4 4" fill="none" stroke="#fff" stroke-width="2"/></svg></span>
  </article>
</section>

<section class="about">
  <h2 class="section-title">About Us</h2>
  <div class="title-rule"></div>
  <p>M&amp;T Electric is a full service electrical contracting shop. We offer commercial, residential, light industrial, and agricultural services. We're Velmora Housepilot and Velmora Motorized Shades certified, as well as an authorized Voltaro generator dealer. We've served the valley and surrounding region for over 16 years.</p>
  <p>We've served the valley for over 16 years. M&amp;T Electric is a full service electrical contracting shop. We offer commercial, residential, light industrial, and agricultural services, with certified home automation and shading installs.</p>
  <div class="about-actions">
    <span class="btn btn-primary">Read More</span>
    <span class="btn btn-outline">Contact Us</span>
  </div>
</section>

<section class="gallery">
  <h2 class="section-title">Our Gallery</h2>
  <div class="title-rule"></div>
  <div class="gallery-grid">
    <div class="gallery-item" role="img" aria-label="Mixed-use brick building project"></div>
    <div class="gallery-item" role="img" aria-label="Red brick commercial building"></div>
    <div class="gallery-item" role="img" aria-label="Modern office building exterior"></div>
    <div class="gallery-item" role="img" aria-label="Multi-storey residential building"></div>
    <div class="gallery-item" role="img" aria-label="Building with mountain backdrop"></div>
    <div class="gallery-item" role="img" aria-label="Commercial building with parking"></div>
  </div>
  <svg class="gallery-arrow prev" width="18" height="34" viewBox="0 0 18 34"><path d="M16 2 3 17l13 15" fill="none" stroke="#999" stroke-width="2"/></svg>
  <svg class="gallery-arrow next" width="18" height="34" viewBox="0 0 18 34"><path d="M2 2l13 15L2 32" fill="none" stroke="#999" stroke-width="2"/></svg>
</section>

<section class="testimonials">
  <h2 class="section-title">Our Testimonials</h2>
  <div class="title-rule"></div>
  <article class="testimonial" style="left:130px">
    <div class="avatar" role="img" aria-label="Client portrait"></div>
    <span class="quote">“</span>
    <h4>Good Service</h4>
    <span class="name">Marisol</span>
    <div class="stars"><svg width="80" height="14" viewBox="0 0 80 14"><g fill="#f39a1e"><path id="st" d="M7 0l2 5h5l-4 3 2 5-5-3-5 3 2-5-4-3h5z"/><use href="#st" x="16"/><use href="#st" x="32"/><use href="#st" x="48"/></g><use href="#st" x="64" fill="#ccc"/></svg></div>
    <p>Clean, careful work from start to finish. The crew was on time, explained every step and left the site spotless.</p>
  </article>
  <article class="testimonial" style="left:668px">
    <div class="avatar" role="img" aria-label="Client portrait"></div>
    <span class="quote">“</span>
    <h4>Good Customer Care</h4>
    <span class="name">Elena</span>
    <div class="stars"><svg width="80" height="14" viewBox="0 0 80 14"><g fill="#f39a1e"><use href="#st"/><use href="#st" x="16"/><use href="#st" x="32"/><use href="#st" x="48"/></g><use href="#st" x="64" fill="#ccc"/></svg></div>
    <p>Our new lighting and shades work perfectly. Friendly team, fair pricing and quick replies to every question we had.</p>
  </article>
</section>

<footer class="site-footer">
  <div class="footer-brand">M&amp;T Electric</div>
  <div class="socials"><span></span><span></span><span></span><span></span></div>
  <div class="footer-col quick-links">
    <h5>Quick Links</h5>
    <ul><li>Home</li><li>Gallery</li><li>Specialty Services</li><li>About</li><li>Services</li><li>Sitemap</li><li>Contact</li></ul>
  </div>
  <div class="footer-col contact">
    <h5>Contact Us</h5>
    <div class="contact-row"><span class="ico"><svg width="14" height="18" viewBox="0 0 14 18"><path d="M7 0a7 7 0 0 1 7 7c0 5-7 11-7 11S0 12 0 7a7 7 0 0 1 7-7z" fill="#fff"/><circle cx="7" cy="7" r="2.5" fill="#444"/></svg></span><div><b>Address</b><small>412 Ridgeview Rd, PO Box 18<br>Millbrook, ST 00000</small></div></div>
    <div class="contact-row"><span class="ico"><svg width="16" height="16" viewBox="0 0 16 16"><path d="M3 1l3 3-2 2c1 2 3 4 5 5l2-2 3 3-2 3C7 15 1 9 1 3z" fill="#fff"/></svg></span><div><b>Phone</b><small>(555) 014-2290</small></div></div>
    <div class="contact-row"><span class="ico"><svg width="16" height="12" viewBox="0 0 16 12"><rect width="16" height="12" fill="#fff"/><path d="M0 0l8 6 8-6" fill="none" stroke="#444" stroke-width="1.5"/></svg></span><div><b>Mail</b><small>info@mandtelectric.example</small></div></div>
  </div>
  <div class="footer-col contact-form">
    <h5>Contact Form</h5>
    <div class="form-row"><span class="field">Name</span><span class="field">Email</span></div>
    <div class="field message">Message</div>
    <span class="btn-submit">Submit</span>
  </div>
  <div class="copyright">Copyright © 2017 M &amp; T Electric. All Right Reserved</div>
</footer>

</body>
</html>
```